Women's Uplift & Praise Luncheon - Matching Poster, flyer and Postcard

We are a Christian Event & Travel Company and we are hosting our inaugural event on June 10, 2017. This event is a Women's Uplift & Praise Luncheon aboard a private yacht leaving out of Crescent Landing, Maryland. The event will cater to women who have a vision to start or have already embarked on the journey of starting or growing a business or ministry. The event calls for a matching poster, flyer and postcard design that give an elegant & exquisite feel with just the right breath of freshness. The colors should reflect our logo as this is our launch event. I have also included 2 photos of the Islandsong Heritage Park production (one of our sponsors) - Please include but do not make it take over the design - this is to advertise the door prize. The final design will portray the branding of the company (Christian, travel, events, elegance, professional), the branding of the event (elegant and luxurious) and the importance of this launch event.
Please include the following information:
Lanternway Event & Travel Group presents
Event name: Rising Tide: Grace, Patience & Devotion.
Tag Line/Description: An Exquisite Women's Uplift & Praise Luncheon.
Guest Speaker: Minister Harriet L. Dunmore (Photo included)
VP of Pinecrest Bank
Asst. Pastor & First Lady of Bethany Grove Baptist Church
Special Guest Psalmist: Minister Tasha Bellamy (Photo Included)
Worship Director of Stillmeadow Community Church
Vocalist, Songwriter, Musician, and Clinician
Venue: Aboard the Sovereign Pearl Yacht
Dock: Crescent Landing
512 Marlowe Quay, Fenwick, MD 20999
Boarding 10:00am
Sailing Promptly at 10:30am
(Please be on time the yacht will not wait)
Date: Saturday June 10, 2017
Tickets: Early Bird US$75.00/person (ends May 15, 2017)
Regular Tickets US$95.99
Purchase Tickets at www.lanternwayevent-travel.example/rising-tide
SPACE IS LIMITED DUE TO YACHT CAPACITY
Grand Prize: Vivienne Laroux Purse
Door Prize: 2 Tickets to the Hawaiian Islandsong Heritage Park
Other prizes for special ladies in attendance.
Ladies are asked to dress in Elegant White Ensemble
Corporate Sponsors:
The Islandsong Heritage Park (Logo included)
J. Ramsey Photography (Logo included)
Special Thanks to our Individual Sponsors:
Mrs. L. Garner, Mr. R Fielding & Mr. T. Ogden

Target Market(s)

Women, Business, Ministry, Christians, Middle to Upper Class

Industry/Entity Type

Events

Font styles to use
Serif
Script

Requirements
Must have
• Elegance, professional, vivid in color & font. be creative in Visual and FONT!
• Poster: 18" X 24"
• Flyer: one sided.
• ***** the final design chosen will have a cross referenced design of 1 flyer, 1 postcard 1 poster. This was included so you have a reference - Be creative!!!!!!
Nice to have
• Matching across all 3 designs (poster, flyer & postcard) but sized appropriately and just enough difference to play up the design and be appealing.
• I uploaded 3 example flyers to give you inspiration of the type of visuals I'm looking for. I removed my amateur sample because the designs were copying it instead of being creative.
Should not have
• Any thing inappropriate, alcohol oriented or sexual

```html
<!DOCTYPE html>
<html lang="en">
<head>
<meta charset="utf-8">
<title>Rising Tide: Grace, Patience &amp; Devotion</title>
<link rel="stylesheet" href="https://fonts.googleapis.com/css2?family=Cinzel:wght@400;700&family=Great+Vibes&family=Playfair+Display:wght@700;900&family=Roboto+Condensed:wght@400;500;700&family=Roboto:wght@400&display=swap">
<style>
  :root {
    --night: #0a0506;
    --ember: #8a1420;
    --wine: #4b0d1c;
    --gold: #f2b432;
    --gold-deep: #c9821a;
    --gold-pale: #ffe08a;
    --orchid: #e85ee0;
    --plum: #4a0a45;
    --plum-deep: #2a0628;
    --plum-edge: #8e2e8a;
    --navy: #1f2a5c;
    --paper: #ffffff;
    --ink: #141414;
    --soft-white: #ece6ee;
  }
  * { box-sizing: border-box; margin: 0; padding: 0; }
  html, body { width: 900px; height: 1200px; overflow: hidden; background: var(--night); }
  .flyer {
    position: relative; width: 900px; height: 1200px; overflow: hidden;
    background:
      radial-gradient(ellipse 520px 300px at 700px 90px, rgba(190,30,50,.75), transparent 70%),
      radial-gradient(ellipse 420px 260px at 120px 80px, rgba(140,20,60,.55), transparent 70%),
      linear-gradient(180deg, var(--wine) 0%, #240709 30%, var(--night) 48%, var(--night) 100%);
    font-family: "Roboto", sans-serif;
  }
  .brand-box {
    position: absolute; left: 154px; top: 156px; width: 255px; height: 172px;
    background: var(--navy);
    display: flex; align-items: center; justify-content: center; gap: 10px; padding: 16px;
  }
  .brand-box .dot { width: 14px; height: 14px; border-radius: 50%; background: var(--gold); flex: none; }
  .brand-box .name {
    font-family: "Cinzel", serif; font-weight: 700; color: var(--gold);
    font-size: 19px; line-height: 1.3; text-align: center;
  }
  .speakers-photo {
    position: absolute; left: 420px; top: 86px; width: 351px; height: 265px;
    background: radial-gradient(ellipse at 40% 40%, #6b4a3e, #3a1a16 60%, rgba(60,10,14,0) 100%),
                linear-gradient(90deg, rgba(240,235,225,.2), rgba(200,20,30,.35));
    border-radius: 8px;
  }
  .title {
    position: absolute; left: 0; width: 900px; top: 332px; text-align: center;
    font-family: "Cinzel", serif; font-weight: 700; font-size: 96px; letter-spacing: 2px;
    color: var(--gold);
    background: linear-gradient(180deg, var(--gold-pale) 10%, var(--gold) 50%, var(--gold-deep) 90%);
    -webkit-background-clip: text; background-clip: text; -webkit-text-fill-color: transparent;
  }
  .subtitle {
    position: absolute; left: 0; width: 900px; top: 418px; text-align: center;
    font-family: "Great Vibes", cursive; font-size: 64px; color: var(--gold); line-height: 1;
  }
  .tagline {
    position: absolute; left: 0; width: 900px; top: 496px; text-align: center;
    font-family: "Cinzel", serif; font-size: 19px; letter-spacing: 1px; color: var(--gold);
  }
  .speaker { position: absolute; text-align: center; }
  .speaker .role { font-size: 22px; line-height: 1.2; }
  .speaker .bio { font-size: 14px; line-height: 1.4; }
  .speaker.guest { left: 20px; width: 500px; top: 556px; color: var(--orchid); }
  .speaker.psalmist { left: 40px; width: 470px; top: 622px; color: #fff6c8; }
  .speaker.psalmist .name { color: var(--gold-pale); }
  .speaker.psalmist .bio { color: var(--gold-pale); }
  .fire-photo {
    position: absolute; left: 560px; top: 548px; width: 340px; height: 182px;
    background: radial-gradient(ellipse at 50% 45%, #d6731c, #6b2a0c 45%, #140808 85%);
  }
  .event-band {
    position: absolute; left: 0; top: 707px; width: 900px; height: 313px;
    background: linear-gradient(90deg, var(--plum-deep) 0%, var(--plum) 45%, #5c1358 100%);
    clip-path: polygon(0 0, 570px 0, 600px 22px, 900px 22px, 900px 100%, 0 100%);
    border-top: 3px solid var(--plum-edge);
  }
  .dance-photo {
    position: absolute; left: 583px; top: 729px; width: 317px; height: 291px;
    background: linear-gradient(160deg, #2d2a22 0%, #6b4b24 45%, #c9a35a 70%, #3c4a1c 100%);
  }
  .venue { position: absolute; left: 0; width: 580px; top: 731px; text-align: center; color: var(--soft-white); }
  .venue .line { font-size: 16.5px; line-height: 24px; }
  .venue .times { font-size: 19px; margin-top: 10px; }
  .venue .note { font-size: 13px; margin-top: 3px; }
  .date {
    position: absolute; left: 25px; top: 848px;
    font-family: "Playfair Display", serif; font-weight: 900; font-size: 52px;
    color: var(--gold); letter-spacing: 1px; transform: scaleX(.92); transform-origin: left;
  }
  .tickets {
    position: absolute; left: 26px; top: 916px;
    font-family: "Roboto Condensed", sans-serif; font-weight: 500; font-size: 20px; color: var(--soft-white);
  }
  .tickets p { line-height: 32px; }
  .tickets .hi { color: var(--gold); }
  .pointer { position: absolute; left: 500px; top: 740px; width: 200px; height: 280px; }
  .footer { position: absolute; left: 0; top: 1020px; width: 900px; height: 180px; background: var(--paper); }
  .sponsor-tab {
    position: absolute; right: 0; top: 0; height: 22px; padding: 0 20px 0 36px;
    background: var(--ink); color: #fff; font-family: "Roboto", sans-serif; font-size: 13px; line-height: 22px;
    clip-path: polygon(0 0, 100% 0, 100% 100%, 18px 100%);
  }
  .limited {
    position: absolute; left: 26px; top: 20px;
    font-family: "Roboto Condensed", sans-serif; font-weight: 500; font-size: 21px; color: var(--ink);
  }
  .prize { position: absolute; left: 0; display: flex; align-items: center; height: 24px; }
  .prize .tag {
    width: 146px; height: 24px; padding-left: 24px;
    background: linear-gradient(180deg, #ffd35a, var(--gold));
    clip-path: polygon(0 0, 132px 0, 146px 50%, 132px 100%, 0 100%);
    font-family: "Roboto Condensed", sans-serif; font-weight: 700; font-size: 16px; line-height: 24px; color: var(--ink);
  }
  .prize .what {
    margin-left: 12px; font-family: "Roboto Condensed", sans-serif; font-weight: 700; font-size: 16px; color: var(--ink);
  }
  .prize.grand { top: 56px; }
  .prize.door { top: 86px; }
  .extras {
    position: absolute; left: 26px; top: 117px; font-size: 15.5px; color: var(--ink); line-height: 23px;
  }
  .extras .script { font-family: "Great Vibes", cursive; font-size: 20px; }
  .partner {
    position: absolute; top: 42px; display: flex; align-items: center; gap: 6px;
    font-family: "Roboto", sans-serif; font-size: 13px; color: var(--ink); line-height: 1.2;
  }
  .partner .mark { width: 12px; height: 12px; flex: none; background: #c8c2c2; }
  .partner.photo { left: 610px; width: 96px; height: 68px; padding: 6px; background: #eeeaea; }
  .partner.park { left: 716px; width: 170px; height: 68px; color: var(--gold-deep); font-weight: 700; font-size: 15px; }
  .partner.park .mark { background: var(--gold); border-radius: 50%; }
  .thanks {
    position: absolute; left: 610px; top: 126px; font-size: 13px; color: var(--ink); line-height: 19px;
  }
</style>
</head>
<body>
<main class="flyer">
  <div class="brand-box"><span class="dot"></span><span class="name">Lanternway Event &amp; Travel Group</span></div>
  <div class="speakers-photo" role="img" aria-label="Portraits of the guest speaker and the special guest psalmist"></div>

  <h1 class="title">RISING TIDE</h1>
  <p class="subtitle">Grace, Patience &amp; Devotion.</p>
  <p class="tagline">An Exquisite Women's Uplift &amp; Praise Luncheon.</p>

  <div class="speaker guest">
    <p class="role">Guest Speaker: <span class="name">Minister Harriet L. Dunmore</span></p>
    <p class="bio">VP of Pinecrest Bank, Asst. Pastor &amp; First Lady of Bethany Grove Baptist Church</p>
  </div>
  <div class="speaker psalmist">
    <p class="role">Special Guest Psalmist: <span class="name">Minister Tasha Bellamy</span></p>
    <p class="bio">Worship Director of Stillmeadow Community Church Vocalist,<br>Songwriter, Musician, and Clinician</p>
  </div>

  <div class="fire-photo" role="img" aria-label="Night fire-knife dancers spinning rings of flame"></div>

  <section class="event-band"></section>
  <div class="dance-photo" role="img" aria-label="Island dancers in grass skirts performing on stage"></div>

  <div class="venue">
    <p class="line">Venue: Aboard the Sovereign Pearl Yacht</p>
    <p class="line">Dock: Crescent Landing, 512 Marlowe Quay, Fenwick, MD 20999</p>
    <p class="times">Boarding 10:00am | Sailing Promptly at 10:30am</p>
    <p class="note">(Please be on time the yacht will not wait)</p>
  </div>

  <p class="date">SATURDAY JUNE 10, 2017</p>
  <div class="tickets">
    <p>Tickets : Early Bird <span class="hi">US$75.00/person</span> (ends May 15, 2017)</p>
    <p>Regular Tickets <span class="hi">US$95.99</span></p>
    <p>Purchase Tickets at <span class="hi">www.lanternwayevent-travel.example/rising-tide</span></p>
  </div>

  <svg class="pointer" viewBox="0 0 200 280" aria-hidden="true">
    <path d="M10 270 C90 230 150 170 165 60" fill="none" stroke="#8e2e8a" stroke-width="6"/>
    <path d="M150 70 L168 40 L182 74 Z" fill="#8e2e8a"/>
  </svg>

  <footer class="footer">
    <div class="sponsor-tab">Corporate Sponsors</div>
    <p class="limited">SPACE IS LIMITED DUE TO YACHT CAPACITY</p>
    <div class="prize grand"><span class="tag">Grand Prize</span><span class="what">Vivienne Laroux Purse</span></div>
    <div class="prize door"><span class="tag">Door Prize</span><span class="what">2 Tickets to the Hawaiian Islandsong Heritage Park</span></div>
    <div class="extras">
      <p>Other prizes for special ladies in attendance.</p>
      <p>Ladies are asked to dress in <span class="script">Elegant White Ensemble</span></p>
    </div>
    <div class="partner photo"><span class="mark"></span><span>J. Ramsey Photography</span></div>
    <div class="partner park"><span class="mark"></span><span>Islandsong Heritage Park</span></div>
    <div class="thanks">
      <p>Special Thanks to our Individual Sponsors:</p>
      <p>Mrs. L. Garner, Mr. R Fielding &amp; Mr. T. Ogden</p>
    </div>
  </footer>
</main>
</body>
</html>
```